Business Card for new Architectural Firm

I intend to practice in a rural mountain community in upstate NY, focusing on residential and light commercial projects, including second home / vacation properties. I wish to convey a feeling of rural outdoorsy modernity.

Color is important - bold and urbane. Secondary or tertiary colors preferred.

Font is important, idiosyncratic is ok

Optionally, I may choose to use the name Brambleford Studio. If used as part of your design, all of the Must Haves are still required.

Images uploaded are logos I like

Industry/Entity Type

Residential

Contact Information for Business Card

Calvin Worthaven
Architect (This word should stand alone or be associated with my name - not license number)
NY License No. 052816
calvin@designbycw.com
607 385 2194

Font styles to use
Sans Serif
Decorative

Requirements
Must have
• Whatever files I need to best utilize your design
• PDF
• JPG
• EPS
• Vectorwhatsit
Nice to have
• Logo or element that can be incorporated into other print material.
• Could be a font based card
Should not have
• no clip art
• No templates
• no floor plans
• no building photographs

```html
<!DOCTYPE html>
<html lang="en">
<head>
<meta charset="utf-8">
<title>Brambleford Studio – Business Card</title>
<link rel="stylesheet" href="https://fonts.googleapis.com/css2?family=Josefin+Sans:wght@300&display=swap">
<style>
  :root {
    --backdrop: #1e1f22;
    --card: #5e2f2e;
    --card-edge: #552a29;
    --ink-light: #efe3df;
    --ink-rose: #d9b3ab;
    --rule: #c99e96;
    --emboss: #7b4541;
  }
  * { margin: 0; padding: 0; box-sizing: border-box; }
  html, body { width: 1200px; height: 1000px; overflow: hidden; }
  body {
    background: var(--backdrop);
    font-family: "Josefin Sans", "Helvetica Neue", Arial, sans-serif;
    font-weight: 300;
    position: relative;
  }
  .card {
    position: absolute;
    width: 540px;
    height: 308px;
    background: var(--card);
    border-radius: 14px;
    box-shadow: 0 14px 30px rgba(0,0,0,0.45);
    border: 1px solid var(--card-edge);
  }
  .card--back { left: 620px; top: 200px; }
  .card--front { left: 40px; top: 500px; }

  .wordmark {
    position: absolute;
    text-transform: uppercase;
    white-space: nowrap;
    text-align: center;
    line-height: 1;
  }
  .wordmark__main {
    display: block;
    font-size: 22px;
    letter-spacing: 2px;
  }
  .wordmark__sub {
    display: block;
    margin-top: 6px;
    font-size: 11px;
    letter-spacing: 7px;
    padding-left: 7px;
  }
  .card--back .wordmark {
    left: 0; right: 0; top: 128px;
    color: var(--emboss);
  }
  .card--front .wordmark {
    left: 30px; top: 96px;
    width: 200px;
    color: var(--ink-light);
  }
  .divider {
    position: absolute;
    left: 262px; top: 40px;
    width: 1px; height: 228px;
    background: var(--rule);
  }
  .identity {
    position: absolute;
    left: 292px; top: 84px;
  }
  .identity__name {
    font-size: 20px;
    color: var(--ink-light);
    letter-spacing: 0.5px;
  }
  .identity__title {
    margin-top: 6px;
    font-size: 11px;
    letter-spacing: 4px;
    color: var(--ink-rose);
    text-transform: uppercase;
  }
  .contact {
    position: absolute;
    left: 292px; top: 190px;
    list-style: none;
  }
  .contact__item {
    display: flex;
    align-items: center;
    gap: 10px;
    font-size: 12px;
    color: var(--ink-rose);
    margin-bottom: 9px;
  }
  .contact__icon { width: 12px; height: 12px; flex: none; }
</style>
</head>
<body>
  <section class="card card--back" aria-label="Card back">
    <div class="wordmark">
      <span class="wordmark__main">Brambleford</span>
      <span class="wordmark__sub">Studio</span>
    </div>
  </section>

  <section class="card card--front" aria-label="Card front">
    <div class="wordmark">
      <span class="wordmark__main">Brambleford</span>
      <span class="wordmark__sub">Studio</span>
    </div>
    <div class="divider"></div>
    <div class="identity">
      <div class="identity__name">Calvin Worthaven</div>
      <div class="identity__title">Architect</div>
    </div>
    <ul class="contact">
      <li class="contact__item">
        <svg class="contact__icon" viewBox="0 0 12 12" aria-hidden="true"><rect x="0.5" y="2" width="11" height="8" fill="#efe3df"/><path d="M0.5 2 L6 6.5 L11.5 2" fill="none" stroke="#5e2f2e" stroke-width="1"/></svg>
        calvin@designbycw.com
      </li>
      <li class="contact__item">
        <svg class="contact__icon" viewBox="0 0 12 12" aria-hidden="true"><path d="M3 1 L5 3.5 L3.8 5 Q5 7.5 7 8.2 L8.5 7 L11 9 L9.5 11 Q3.5 10 1 2.5 Z" fill="#efe3df"/></svg>
        607 385 2194
      </li>
      <li class="contact__item">
        <svg class="contact__icon" viewBox="0 0 12 12" aria-hidden="true"><circle cx="6" cy="6" r="5" fill="none" stroke="#efe3df" stroke-width="1.4"/><path d="M3.5 6 L5.3 7.8 L8.6 4.3" fill="none" stroke="#efe3df" stroke-width="1.4"/></svg>
        NY License No. 052816
      </li>
    </ul>
  </section>
</body>
</html>
```